Coastline Premier Retreats Business Card Design

Design a business card for Coastline Premier Retreats. Look at the website for colors and reference. Card should have logo, name, title, office number, mobile number, email, URL and a tagline like, "Luxury Hotel & Resort Email Marketing" (This might change).

https://www.coastlinepremierretreats.example

The rest I will leave up to your imagination.

Contact Information for Business Card

Logo, name, title, office number, mobile number, email, URL and a tagline like, "Luxury Hotel & Resort Email Marketing" (This might change).

```html
<!DOCTYPE html>
<html lang="en">
<head>
<meta charset="utf-8">
<title>Coastline Premier Retreats – Business Card</title>
<link rel="stylesheet" href="https://fonts.googleapis.com/css2?family=Open+Sans:wght@400;600;700&display=swap">
<style>
  :root {
    --stage: #232323;
    --card: #1e1e21;
    --accent: #f07018;
    --ink: #ffffff;
    --shadow: rgba(0, 0, 0, 0.55);
  }
  * { margin: 0; padding: 0; box-sizing: border-box; }
  html, body {
    width: 1200px; height: 780px; overflow: hidden;
    background: var(--stage);
    font-family: "Open Sans", Arial, sans-serif;
    color: var(--ink);
  }
  .stage {
    width: 1200px; height: 780px;
    display: flex; align-items: center; justify-content: center; gap: 70px;
  }
  .card {
    position: relative;
    width: 380px; height: 640px;
    background: var(--card);
    border-radius: 26px;
    border: 2px solid var(--accent);
    box-shadow: 0 18px 40px var(--shadow);
    overflow: hidden;
  }

  /* Front */
  .card-front .brand-vertical {
    position: absolute; left: 50%; top: 50%;
    transform: translate(-50%, -50%) rotate(-90deg);
    white-space: nowrap;
    font-weight: 700; font-size: 34px; letter-spacing: 1px;
    text-transform: uppercase;
    color: var(--ink);
  }

  /* Back */
  .card-back .brand {
    position: absolute; left: 40px; top: 46px;
    display: flex; align-items: center; gap: 12px;
    font-weight: 700; font-size: 17px; letter-spacing: 0.5px;
    text-transform: uppercase; color: var(--ink);
  }
  .brand-square { width: 14px; height: 14px; background: var(--accent); flex: none; }

  .profile { position: absolute; left: 40px; right: 30px; bottom: 52px; }
  .person-name { font-weight: 700; font-size: 32px; line-height: 1.1; }
  .person-name .first { color: var(--accent); }
  .person-role { font-weight: 600; font-size: 15px; margin-top: 2px; }
  .tagline { color: var(--accent); font-size: 15px; line-height: 1.35; margin-top: 18px; }
  .contacts { list-style: none; margin-top: 18px; }
  .contacts li {
    display: flex; align-items: center; gap: 10px;
    font-size: 13.5px; line-height: 1.9;
  }
  .contacts svg { width: 15px; height: 15px; flex: none; }
</style>
</head>
<body>
<main class="stage">
  <section class="card card-front" aria-label="Card front">
    <p class="brand-vertical">Coastline Premier Retreats</p>
  </section>

  <section class="card card-back" aria-label="Card back">
    <div class="brand"><span class="brand-square"></span>Coastline Premier Retreats</div>

    <div class="profile">
      <h1 class="person-name"><span class="first">Lena</span> Marvick</h1>
      <p class="person-role">Co-Founder</p>
      <p class="tagline">Luxury Hotel &amp;<br>Resort Email Marketing</p>
      <ul class="contacts">
        <li>
          <svg viewBox="0 0 16 16" aria-hidden="true"><path fill="var(--accent)" d="M3.6 1.5l2.3 2.6-1.3 1.6c.9 2 2.5 3.6 4.6 4.6l1.6-1.3 2.6 2.3-1.4 2.2C7.2 13.4 2.6 8.8 1.5 3z"/></svg>
          (555) 014-2758
        </li>
        <li>
          <svg viewBox="0 0 16 16" aria-hidden="true"><rect x="4" y="1.5" width="8" height="13" rx="1.5" fill="none" stroke="var(--accent)" stroke-width="1.5"/><circle cx="8" cy="12" r="0.9" fill="var(--accent)"/></svg>
          (555) 014-7777
        </li>
        <li>
          <svg viewBox="0 0 16 16" aria-hidden="true"><g fill="none" stroke="var(--accent)" stroke-width="1.3"><circle cx="8" cy="8" r="6.2"/><ellipse cx="8" cy="8" rx="2.7" ry="6.2"/><path d="M1.8 8h12.4"/></g></svg>
          www.coastlinepremierretreats.example
        </li>
        <li>
          <svg viewBox="0 0 16 16" aria-hidden="true"><g fill="none" stroke="var(--accent)" stroke-width="1.4"><rect x="1.5" y="3.5" width="13" height="9" rx="1"/><path d="M1.8 4l6.2 5 6.2-5"/></g></svg>
          info@coastlinepremierretreats.example
        </li>
      </ul>
    </div>
  </section>
</main>
</body>
</html>
```